Venture 482 - Lumora Book Cover

I am looking for a Lumora book cover for my book about "Venture 482".
The Book is Titled:
Venture 482 Ascended
Shaping Outcomes: Paths To Unlocking Cosmic Truths
Author is Dorian Pell
Here is a book description that may help you understand more about it:
Inspired by the genius of Edwin Marlowe, this comprehensive guide delves into the ancient wisdom and cutting-edge science behind the 482 method, a powerful tool for manifesting your desires. Whether you're seeking personal growth, financial success, or spiritual enlightenment, this book provides advanced techniques and methods to transform your dreams into reality.
Any questions please ask.
Thanks
Owen

```html
<!DOCTYPE html>
<html lang="en">
<head>
<meta charset="utf-8">
<title>Venture 482 Ascended — Dorian Pell</title>
<link rel="stylesheet" href="https://fonts.googleapis.com/css2?family=League+Spartan:wght@700;800&family=Josefin+Sans:wght@300;400&family=Montserrat:wght@300;400&display=swap">
<style>
  :root {
    --page-bg: #e9e8e6;
    --night: #05081a;
    --deep-blue: #14214f;
    --violet: #5b4f8e;
    --glow: #fff3dc;
    --amber: #b8873f;
    --cream: #fdeee0;
    --gold: #d8c152;
    --indigo: #3b4a9a;
    --white: #f4f2f0;
  }
  html, body {
    margin: 0;
    width: 1200px;
    height: 1131px;
    overflow: hidden;
    background: var(--page-bg);
  }
  .cover {
    position: absolute;
    left: 231px;
    top: 0;
    width: 737px;
    height: 1131px;
    overflow: hidden;
    background: var(--night);
  }
  .cover-scene {
    position: absolute;
    inset: 0;
    background:
      radial-gradient(ellipse 210px 260px at 50% 66%, var(--glow) 0%, rgba(255,236,200,0.85) 30%, rgba(184,135,63,0.55) 60%, rgba(184,135,63,0) 100%),
      radial-gradient(ellipse 420px 360px at 50% 50%, rgba(91,79,142,0.75) 0%, rgba(20,33,79,0.6) 55%, rgba(5,8,26,0) 100%),
      linear-gradient(to bottom, var(--night) 0%, var(--deep-blue) 30%, #1c1d3a 62%, #0d1224 86%, #0a0f1f 100%);
  }
  .author {
    position: absolute;
    top: 78px;
    left: 0;
    width: 100%;
    text-align: center;
    font-family: "Josefin Sans", sans-serif;
    font-weight: 300;
    font-size: 46px;
    letter-spacing: 0.32em;
    padding-left: 0.32em;
    box-sizing: border-box;
    color: var(--cream);
    margin: 0;
  }
  .title {
    margin: 0;
    font-family: "League Spartan", sans-serif;
  }
  .title-line {
    position: absolute;
    left: 0;
    width: 100%;
    text-align: center;
    display: block;
    line-height: 1;
  }
  .title-word {
    top: 226px;
    font-weight: 800;
    font-size: 106px;
    letter-spacing: -0.04em;
    color: var(--cream);
  }
  .title-number {
    top: 296px;
    font-weight: 800;
    font-size: 300px;
    letter-spacing: -0.02em;
    color: var(--gold);
    text-shadow: 0 6px 18px rgba(0,0,0,0.35);
  }
  .title-edition {
    top: 553px;
    font-weight: 800;
    font-size: 52px;
    letter-spacing: 0.42em;
    padding-left: 0.42em;
    box-sizing: border-box;
    color: var(--indigo);
  }
  .subtitle {
    position: absolute;
    top: 978px;
    left: 0;
    width: 100%;
    text-align: center;
    color: var(--white);
    margin: 0;
  }
  .subtitle-lead {
    display: block;
    font-family: "Montserrat", sans-serif;
    font-weight: 400;
    font-size: 30px;
    letter-spacing: 0.01em;
    line-height: 1.2;
  }
  .subtitle-body {
    display: block;
    font-family: "Montserrat", sans-serif;
    font-weight: 400;
    font-size: 26px;
    line-height: 1.3;
    margin-top: 6px;
  }
</style>
</head>
<body>
  <main class="cover">
    <div class="cover-scene" role="img" aria-label="Photograph of a person seen from behind standing on a forest road at night, shading their eyes from a bright glowing light beneath a starry violet sky"></div>
    <p class="author">DORIAN PELL</p>
    <h1 class="title">
      <span class="title-line title-word">VENTURE</span>
      <span class="title-line title-number">482</span>
      <span class="title-line title-edition">ASCENDED</span>
    </h1>
    <p class="subtitle">
      <span class="subtitle-lead">SHAPING OUTCOMES:</span>
      <span class="subtitle-body">Paths to unlocking<br>cosmic truths</span>
    </p>
  </main>
</body>
</html>
```